Willow Cradle Pregnancy and Baby Massage

I need a web design for a new business, WILLOW CRADLE PREGNANCY AND BABY MASSAGE that I am in the process of setting up in the suburbs of Perth, Western Australia. The business is owned and operated by myself and my intention is to service Pregnant Mothers and Parents of Young Babies that would benefit from massage. I would like to have a "Home Page" and pages for "About Me", "Pregnancy Massage", "Baby Massage", a Pricing Page for Pregnancy Massage Sessions, a Pricing Page for Baby Massage Sessions, and a "Contact Me" page to allow clients to either contact me with queries or book available pregnancy massage sessions on a particular day of the week. I would also like a "News" page that would include articles I have written, news about new courses and a link to my Facebook page (yet to be set up). I would like to keep the colour schemes similar to my logo design colours. I need the design to be easy to follow and to appeal to a younger audience (20's to mid 30's).
The target audience is pregnant mothers-to-be wishing to receive massage treatments, and new parents and grandparents of small babies that would like to learn how to massage their babies.
The look and feel should be modern, professional, elegant and feminine.
I need the design to be in a standard format such that I can update the content by myself ( and does not need specialised software) as the company and business progresses.

Target Market(s)

Contact Information for Business Card

Card should have rounded edges. Design should have the same "feel" as the website. Contact Details of my business address, mobile phone, email and website should be included.

Font styles to use
Script

Requirements
Must have
• Same colours as logo design. In cmyk system, the colours are: 20,60,0,0 which best result is pantone 681 and 40,40,0,0 which best result is pantone 2645. Card should include the logo design.

```html
<!DOCTYPE html>
<html lang="en">
<head>
<meta charset="utf-8">
<title>Willow Cradle Pregnancy and Baby Massage – Pregnancy Massage Sessions</title>
<link href="https://fonts.googleapis.com/css2?family=Handlee&family=Rosario:wght@400&display=swap" rel="stylesheet">
<style>
  :root{
    --teal:#97bdb7;
    --menu-purple:#4a3a6e;
    --menu-pink:#e060a4;
    --menu-text:#c9ece6;
    --blush:#f7e3e6;
    --page-dim:#aaa3a4;
    --band-dim:#b4aaad;
    --heading-purple:#7d5f9e;
    --accent-pink:#c0507c;
    --row-rose:#9b6f82;
    --row-plum:#7a6b86;
    --ink:#2e2a30;
    --brand:#d4488f;
  }
  *{box-sizing:border-box;margin:0;padding:0}
  html,body{width:874px;height:1200px;overflow:hidden}
  body{position:relative;background:var(--page-dim);font-family:"Rosario",sans-serif;color:var(--ink)}

  .top-bar{position:absolute;left:0;top:0;width:874px;height:95px;background:var(--teal)}
  .close-icon{position:absolute;left:328px;top:26px}
  .brand{position:absolute;left:470px;top:14px;width:230px;text-align:center;color:var(--brand);font-family:"Handlee",cursive;line-height:1}
  .brand-name{display:block;font-size:30px}
  .brand-tag{display:block;font-size:13px;margin-top:6px}
  .search-icon{position:absolute;left:770px;top:24px}

  .page{position:absolute;left:0;top:95px;width:874px;height:1005px}
  .crumb{position:absolute;left:292px;top:34px;width:40px;height:26px;background:var(--band-dim)}
  .title-band{position:absolute;left:0;top:95px;width:874px;height:95px;background:var(--band-dim)}
  .page-title{position:absolute;left:260px;top:23px;width:560px;text-align:center;font-family:"Handlee",cursive;font-weight:400;font-size:42px;color:var(--heading-purple)}
  .session-name{position:absolute;left:40px;top:232px;font-family:"Handlee",cursive;font-weight:400;font-size:24px;color:var(--accent-pink)}
  .details-band{position:absolute;left:0;top:320px;width:874px;height:423px;background:var(--band-dim)}
  .details{position:absolute;left:20px;top:30px;width:840px;text-align:center;font-size:28px;line-height:38px}
  .price-row{position:absolute;left:0;width:874px;font-size:28px;padding-left:300px;display:flex;align-items:center}
  .price-row.rose{top:781px;height:114px;background:var(--row-rose)}
  .price-row.plum{top:895px;height:110px;background:var(--row-plum)}

  .side-menu{position:absolute;left:0;top:0;width:312px;height:1100px;background:var(--blush)}
  .menu-list{list-style:none;background:var(--menu-purple);height:705px}
  .menu-list li{display:flex;align-items:center;justify-content:center;text-align:center;border-bottom:3px dashed var(--menu-pink);font-family:"Handlee",cursive;color:var(--menu-text);white-space:nowrap}
  .m-home{height:90px;font-size:36px}
  .m-about{height:104px;font-size:30px}
  .m-small{font-size:21px}
  .m-1{height:95px}.m-2{height:101px}.m-3{height:120px}.m-4{height:99px}
  .m-contact{height:96px;font-size:30px}

  .footer{position:absolute;left:0;top:1100px;width:874px;height:100px;background:var(--teal)}
  .social{position:absolute;top:32px;width:36px;height:36px;border-radius:50%;background:var(--brand)}
</style>
</head>
<body>
  <header class="top-bar">
    <svg class="close-icon" width="48" height="48" viewBox="0 0 48 48" aria-label="Close menu"><path d="M6 6 L42 42 M42 6 L6 42" stroke="#d4488f" stroke-width="7" stroke-linecap="round"/></svg>
    <div class="brand"><span class="brand-name">Willow Cradle</span><span class="brand-tag">Pregnancy and Baby Massage</span></div>
    <svg class="search-icon" width="52" height="52" viewBox="0 0 52 52" aria-label="Search"><circle cx="21" cy="21" r="15" fill="none" stroke="#d4488f" stroke-width="6"/><path d="M32 32 L47 47" stroke="#d4488f" stroke-width="7" stroke-linecap="round"/></svg>
  </header>

  <main class="page">
    <div class="crumb"></div>
    <section class="title-band"><h1 class="page-title">Pregnancy Massage Sessions Available</h1></section>
    <h2 class="session-name">Pregnancy Massage Session</h2>
    <section class="details-band">
      <p class="details">Each session begins with a consultation to assess any needs, and to review any changes the body has undergone since the last session. This way the massage can be tailored and given in a safe manner. A side-lying position is used with pillows for support. This is a comfortable position, and minimises pressure on one side's blood vessels. This reduces the risk of Supine Hypotension, which can cause dizziness and fainting. In this position, there is no pressure on the lower back.</p>
    </section>
    <div class="price-row rose">60 mins session</div>
    <div class="price-row plum">- including 15 mins consultation.</div>
  </main>

  <nav class="side-menu">
    <ul class="menu-list">
      <li class="m-home">Home</li>
      <li class="m-about">About me</li>
      <li class="m-small m-1">Benefits of pregnancy massage</li>
      <li class="m-small m-2">Benefits of baby massage</li>
      <li class="m-small m-3">Pregnancy Massage Sessions</li>
      <li class="m-small m-4">Baby Massage Sessions</li>
      <li class="m-contact">Contact</li>
    </ul>
  </nav>

  <footer class="footer">
    <span class="social" style="left:77px"></span>
    <span class="social" style="left:243px"></span>
    <span class="social" style="left:408px"></span>
    <span class="social" style="left:582px"></span>
    <span class="social" style="left:770px"></span>
  </footer>
</body>
</html>
```